Security based company delivering High Risk Training to Law Enforcement Agencies Worldwide.

We need a Web design for a company doing business in Washington D.C. We deliver High Risk Training to Law Enforcement Agencies throughout the world. Our focus is on Improvised Explosive Devices. We train Bomb Technicians and First Responders in all aspects relating to bombings and criminal incidents globally.
Updates

Reason: We have uploaded our logo. Thank you.

Target Market(s)

Military and Law Enforcement Personnel from around the world.

Industry/Entity Type

Business

Requirements
Should not have
• Do not include cartoon like characters.

```html
<!DOCTYPE html>
<html lang="en">
<head>
<meta charset="utf-8">
<title>Vantrek International</title>
<link rel="stylesheet" href="https://fonts.googleapis.com/css2?family=Arimo:wght@400;700&family=Open+Sans:wght@400;600&display=swap">
<style>
  :root {
    --red: #d0191b;
    --red-dark: #b51214;
    --ink: #111;
    --body: #333;
    --muted: #555;
    --charcoal: #2d2d2d;
    --line: #d7d7d7;
    --sand-1: #c9b39a;
    --sand-2: #a89582;
    --smoke: #3a3430;
  }
  * { box-sizing: border-box; margin: 0; padding: 0; }
  html, body { width: 1200px; height: 1196px; overflow: hidden; }
  body {
    position: relative;
    font-family: "Arimo", Arial, sans-serif;
    color: var(--body);
    background: linear-gradient(#fff 0, #fff 634px, #eeeeee 640px, #fff 790px, #fff 100%);
  }
  .top-bar { position: absolute; top: 0; left: 0; width: 1200px; height: 7px; background: var(--red); }

  .brand { position: absolute; left: 140px; top: 50px; display: flex; align-items: center; gap: 12px; }
  .brand-mark { width: 34px; height: 34px; background: var(--red); }
  .brand-name { font-size: 30px; font-weight: 700; color: var(--ink); letter-spacing: 1px; }

  .search {
    position: absolute; left: 786px; top: 28px; width: 275px; height: 28px;
    border: 1px solid #ddd; border-radius: 14px; background: #fff;
    display: flex; align-items: center; padding-left: 14px;
    font-size: 12px; color: #999;
  }
  .search-btn { position: absolute; right: 0; top: 0; width: 34px; height: 26px; border-left: 1px solid #ddd; display: flex; align-items: center; justify-content: center; }

  .account { position: absolute; right: 139px; top: 87px; font-size: 17px; color: var(--ink); word-spacing: 4px; }

  .main-nav {
    position: absolute; left: 138px; top: 136px; width: 923px; height: 42px;
    background: linear-gradient(var(--red), var(--red-dark)); border-radius: 4px 4px 0 0;
    display: flex;
  }
  .main-nav a {
    display: flex; align-items: center; justify-content: center;
    color: #fff; font-size: 13px; font-weight: 700; text-decoration: none;
    border-right: 1px solid rgba(255,255,255,0.18);
  }
  .main-nav a:last-child { border-right: 0; }
  .main-nav a.is-active { background: var(--charcoal); color: #ff6d6d; border-radius: 4px 0 0 0; }

  .hero {
    position: absolute; left: 0; top: 178px; width: 1200px; height: 456px;
    background: radial-gradient(ellipse at 48% 55%, var(--smoke) 0, #6b5f55 18%, var(--sand-2) 38%, var(--sand-1) 70%, #d8c7b3 100%);
  }
  .hero-caption {
    position: absolute; left: 609px; top: 287px; width: 452px; height: 190px;
    background: rgba(40,40,40,0.78); border-radius: 3px; padding: 18px 16px;
  }
  .hero-caption h2 { font-family: "Open Sans", Arial, sans-serif; font-weight: 600; font-size: 24px; color: #fff; margin-bottom: 8px; }
  .hero-caption h2 span { color: var(--red); }
  .hero-caption p { font-size: 13px; line-height: 22px; color: #eee; }
  .hero-arrow {
    position: absolute; top: 385px; width: 41px; height: 41px; background: rgba(40,40,40,0.85);
    display: flex; align-items: center; justify-content: center;
  }
  .hero-arrow.prev { left: 0; }
  .hero-arrow.next { right: 0; }
  .hero-dots { position: absolute; left: 556px; top: 544px; display: flex; gap: 10px; }
  .hero-dots i { width: 14px; height: 14px; border-radius: 50%; background: #fff; }
  .hero-dots i.is-active { background: var(--red); }

  .welcome {
    position: absolute; left: 139px; top: 590px; width: 922px; height: 188px;
    background: #fff; border-radius: 4px 4px 0 0; text-align: center; padding-top: 13px;
  }
  .section-title { font-size: 24px; font-weight: 400; color: var(--muted); }
  .section-title span { color: var(--red); }
  .welcome p { margin: 12px 14px 0; font-size: 13px; line-height: 23px; color: var(--body); }
  .btn {
    display: inline-block; padding: 0 10px; height: 29px; line-height: 29px;
    background: var(--charcoal); color: #fff; font-size: 13px; border-radius: 3px;
  }
  .btn.is-red { background: var(--red); }
  .welcome .btn { margin-top: 12px; width: 85px; padding: 0; }

  .rule { position: absolute; left: 139px; width: 922px; height: 1px; background: var(--line); }

  .services-title { position: absolute; left: 139px; top: 810px; width: 922px; text-align: center; }
  .services-nav { position: absolute; left: 996px; top: 810px; display: flex; gap: 8px; }
  .services-nav span { width: 28px; height: 27px; border-radius: 2px; background: var(--charcoal); display: flex; align-items: center; justify-content: center; }
  .services-nav span.next { background: var(--red); }

  .services { position: absolute; left: 139px; top: 862px; display: flex; gap: 22px; }
  .service-card {
    width: 214px; height: 297px; border: 1px solid #ddd; border-radius: 4px; background: #fff;
    overflow: hidden; text-align: center;
  }
  .service-card.is-featured { background: #f2f2f2; }
  .service-photo { height: 140px; }
  .service-card h3 { font-size: 17px; font-weight: 400; color: var(--red); margin-top: 10px; }
  .service-card p { text-align: left; font-size: 13px; line-height: 22px; color: var(--ink); margin: 4px 9px 0; height: 70px; }
  .service-card .btn { margin-top: 10px; height: 25px; line-height: 25px; font-size: 13px; padding: 0 6px; }

  .photo-car-fire { background: linear-gradient(135deg, #c8b9a5, #e0a050 60%, #c9b39a); }
  .photo-blast-sand { background: linear-gradient(#b8b4b8, #c9b59c 55%, #bfa888); }
  .photo-bomb-suit { background: linear-gradient(135deg, #d5d0c8, #6e7152 55%, #b7a58d); }
  .photo-debris { background: linear-gradient(#aeb3bd, #9c8d7d 50%, #c6ae92); }
</style>
</head>
<body>
  <div class="top-bar"></div>

  <div class="brand">
    <div class="brand-mark"></div>
    <div class="brand-name">Vantrek International</div>
  </div>

  <div class="search">Search_
    <span class="search-btn">
      <svg width="12" height="12" viewBox="0 0 12 12"><circle cx="5" cy="5" r="3.6" fill="none" stroke="#d0191b" stroke-width="1.8"/><line x1="7.6" y1="7.6" x2="11" y2="11" stroke="#d0191b" stroke-width="2"/></svg>
    </span>
  </div>

  <div class="account">Login &nbsp;|&nbsp; Sign Up</div>

  <nav class="main-nav">
    <a class="is-active" style="width:66px">Home</a>
    <a style="width:81px">About Us</a>
    <a style="width:106px">Lorem Ipsum</a>
    <a style="width:105px">Consectetuer</a>
    <a style="width:112px">Adipiscing Elit</a>
    <a style="width:154px">Nostrud Exerci Tation</a>
    <a style="width:171px">Consectetuer Adipiscing</a>
    <a style="width:127px">Tation Ullamco</a>
  </nav>

  <section class="hero" role="img" aria-label="Training scene: a car engulfed by a detonation with smoke and fire in a desert range"></section>
  <div class="hero-caption">
    <h2><span>Consectetuer</span> Adipiscing Elit</h2>
    <p>Lorem ipsum dolor sit amet, consectetuer adipiscing elit, sed diam nonummy nibh euismod tincidunt ut laoreet dolore magna aliquam erat volutpat. Ut wisi enim ad minim veniam, quis nostrud exerci tation ullamcorper suscipit lobortis nisl ut aliquip ex ea commodo consequat. Duis autem vel eum iriure dolor in hendrerit.</p>
  </div>
  <div class="hero-arrow prev"><svg width="14" height="16" viewBox="0 0 14 16"><path d="M10 2 4 8l6 6" fill="none" stroke="#fff" stroke-width="3"/></svg></div>
  <div class="hero-arrow next"><svg width="14" height="16" viewBox="0 0 14 16"><path d="M4 2l6 6-6 6" fill="none" stroke="#fff" stroke-width="3"/></svg></div>
  <div class="hero-dots"><i></i><i></i><i class="is-active"></i><i></i></div>

  <section class="welcome">
    <h1 class="section-title">Welcome to <span>Vantrek International</span></h1>
    <p>Lorem ipsum dolor sit amet, consectetuer adipiscing elit, sed diam nonummy nibh euismod tincidunt ut laoreet dolore magna aliquam erat volutpat. Ut wisi enim ad minim veniam, quis nostrud exerci tation ullamcorper suscipit lobortis nisl ut aliquip ex ea commodo consequat. Duis autem vel eum iriure dolor in hendrerit in vulputate velit esse molestie consequat, vel illum dolore eu feugiat nulla facilisis at vero eros et accumsan et iusto odio dignissim qui blandit praesent luptatum zzril delenit augue duis dolore te feugait nulla facilisi.</p>
    <span class="btn">Read More</span>
  </section>

  <div class="rule" style="top:793px"></div>

  <h2 class="section-title services-title">Vantrek International <span>Services</span></h2>
  <div class="services-nav">
    <span><svg width="10" height="12" viewBox="0 0 10 12"><path d="M7 1 2 6l5 5" fill="none" stroke="#fff" stroke-width="2.4"/></svg></span>
    <span class="next"><svg width="10" height="12" viewBox="0 0 10 12"><path d="M3 1l5 5-5 5" fill="none" stroke="#fff" stroke-width="2.4"/></svg></span>
  </div>

  <div class="services">
    <article class="service-card">
      <div class="service-photo photo-car-fire" role="img" aria-label="Car burning after a controlled blast"></div>
      <h3>Consectetuer adipiscing</h3>
      <p>Lorem ipsum dolor sit amet, consectetuer adipiscing elit, sed diam nonummy nibh.</p>
      <span class="btn">Read More</span>
    </article>
    <article class="service-card is-featured">
      <div class="service-photo photo-blast-sand" role="img" aria-label="Sand plume from a ground detonation"></div>
      <h3>Consectetuer adipiscing</h3>
      <p>Lorem ipsum dolor sit amet, consectetuer adipiscing elit, sed diam nonummy nibh.</p>
      <span class="btn is-red">Read More</span>
    </article>
    <article class="service-card">
      <div class="service-photo photo-bomb-suit" role="img" aria-label="Bomb technician in protective suit handling equipment"></div>
      <h3>Consectetuer adipiscing</h3>
      <p>Lorem ipsum dolor sit amet, consectetuer adipiscing elit, sed diam nonummy nibh.</p>
      <span class="btn">Read More</span>
    </article>
    <article class="service-card">
      <div class="service-photo photo-debris" role="img" aria-label="Debris thrown up by an explosion on a range"></div>
      <h3>Consectetuer adipiscing</h3>
      <p>Lorem ipsum dolor sit amet, consectetuer adipiscing elit, sed diam nonummy nibh.</p>
      <span class="btn">Read More</span>
    </article>
  </div>

  <div class="rule" style="top:1188px"></div>
</body>
</html>
```